Brindlewood Elementary School 2019-2020 Priority Goals

This visual will encapsulate our school's annual goals. We are a large elementary school in a high performing school district. We base our annual goals primarily on our school generated set of foundational promises. We know that the relationships of the people are critical to our success. The product will primarily be used with our staff internally to keep focused on our priority goals for the year, which are to innovate and collaborate. The collaboration is both amongst staff and also in stronger partnerships with our parent community. The innovation is in not settling for how things have always been done and will focus in three areas: future ready skills, academic growth and achievement and finally in social/emotional growth. We have been saying to one another that "we will accelerate the academic and social emotional growth of the students we serve by innovating and collaborating.

Target Market(s)

Staff, parents and school board

Industry/Entity Type

Education

Font styles to use
Other font styles liked:
• open to your ideas

Colors
0255a3
fbed22

Requirements
Must have
• pretty new to this idea, we'll attach the early sketches below. You'll also find a school logo design as well as the promises that are referred to in the sketch.
Nice to have
• the colors below are school colors, but we are open to your creative genius as well.

```html
<!DOCTYPE html>
<html lang="en">
<head>
<meta charset="utf-8">
<title>Brindlewood Elementary School – Foundation Believe &amp; Promises</title>
<link rel="stylesheet" href="https://fonts.googleapis.com/css2?family=Cabin:wght@400;500&family=Roboto+Condensed:wght@700&family=Figtree:wght@400&display=swap">
<style>
  :root {
    --school-blue: #0255a3;
    --school-yellow: #fbed22;
    --paper: #ffffff;
  }
  html, body {
    margin: 0;
    padding: 0;
    width: 1200px;
    height: 1200px;
    overflow: hidden;
    background: var(--paper);
  }
  .poster {
    display: block;
    width: 1200px;
    height: 1200px;
  }
  .poster-title {
    font-family: "Cabin", "Gill Sans", sans-serif;
    font-weight: 400;
    font-size: 92px;
    fill: var(--school-blue);
  }
  .heart-fill { fill: var(--school-yellow); }
  .heart-outline {
    fill: none;
    stroke: var(--school-blue);
    stroke-width: 7;
    stroke-linecap: round;
  }
  .outline-gap {
    fill: none;
    stroke: var(--paper);
    stroke-width: 34;
    stroke-linecap: butt;
  }
  .outline-label {
    font-family: "Figtree", "Helvetica Neue", sans-serif;
    font-size: 25px;
    fill: var(--school-blue);
    letter-spacing: 0.5px;
    dominant-baseline: central;
  }
  .mission,
  .pillar,
  .pillar-detail,
  .school-name {
    font-family: "Roboto Condensed", "Arial Narrow", sans-serif;
    font-weight: 700;
    fill: var(--school-blue);
    text-anchor: middle;
  }
  .mission { font-size: 35px; }
  .pillar { font-size: 39px; }
  .pillar-detail { font-size: 27px; }
  .branch {
    stroke: var(--school-blue);
    stroke-width: 2;
    fill: none;
  }
  .school-name { font-size: 50px; text-anchor: start; }
  .school-mark { fill: var(--school-blue); }
</style>
</head>
<body>
<svg class="poster" viewBox="0 0 1500 1500" xmlns="http://www.w3.org/2000/svg">
  <defs>
    <path id="label-top-left" d="M440 214 Q525 190 610 214"/>
    <path id="label-top-right" d="M822 246 C 900 200 1110 200 1222 300"/>
    <path id="label-left" d="M236 560 Q252 640 306 700"/>
    <path id="label-lower-left" d="M415 848 L 668 1103"/>
    <path id="label-right" d="M1152 745 Q1225 680 1250 598"/>
    <path id="label-lower-right" d="M880 1058 L 990 946"/>
  </defs>

  <text class="poster-title" x="750" y="128" text-anchor="middle">Foundation Believe &amp; Promises</text>

  <path class="heart-fill" d="M750 390 C 700 300, 600 235, 480 240 C 340 245, 262 350, 262 470 C 262 640, 420 800, 560 950 C 640 1035, 710 1100, 750 1140 C 790 1100, 860 1035, 940 950 C 1080 800, 1238 640, 1238 470 C 1238 350, 1160 245, 1020 240 C 900 235, 800 300, 750 390 Z"/>

  <path class="heart-outline" d="M750 335 C 700 260, 600 205, 470 210 C 320 215, 232 330, 232 460 C 232 650, 400 820, 540 975 C 630 1075, 700 1130, 750 1178 C 800 1130, 870 1075, 960 975 C 1100 820, 1270 650, 1270 460 C 1270 330, 1180 215, 1035 212 C 900 210, 800 265, 750 335"/>

  <g class="outline-gaps">
    <use class="outline-gap" href="#label-top-left"/>
    <use class="outline-gap" href="#label-top-right"/>
    <use class="outline-gap" href="#label-left"/>
    <use class="outline-gap" href="#label-lower-left"/>
    <use class="outline-gap" href="#label-right"/>
    <use class="outline-gap" href="#label-lower-right"/>
  </g>

  <g class="outline-labels">
    <text class="outline-label"><textPath href="#label-top-left" startOffset="50%" text-anchor="middle">Relationships</textPath></text>
    <text class="outline-label"><textPath href="#label-top-right" startOffset="50%" text-anchor="middle">Listen ! Every student has a song</textPath></text>
    <text class="outline-label"><textPath href="#label-left" startOffset="50%" text-anchor="middle">Marla Quinlan</textPath></text>
    <text class="outline-label"><textPath href="#label-lower-left" startOffset="50%" text-anchor="middle">Listening for student's song</textPath></text>
    <text class="outline-label"><textPath href="#label-right" startOffset="50%" text-anchor="middle">Relationships</textPath></text>
    <text class="outline-label"><textPath href="#label-lower-right" startOffset="50%" text-anchor="middle">Marla Quinlan</textPath></text>
  </g>

  <g class="mission-statement">
    <text class="mission" x="750" y="435">We will accelerate the</text>
    <text class="mission" x="750" y="481">academic &amp; social/emotional growth</text>
    <text class="mission" x="750" y="528">of the students we serve by :</text>
  </g>

  <g class="pillar-innovating">
    <text class="pillar" x="512" y="627">Innovating</text>
    <text class="pillar-detail" x="512" y="659">Agents of change</text>
    <text class="pillar-detail" x="512" y="685">Learners</text>
    <line class="branch" x1="422" y1="694" x2="422" y2="713"/>
    <line class="branch" x1="512" y1="694" x2="512" y2="713"/>
    <line class="branch" x1="602" y1="694" x2="602" y2="713"/>
    <text class="pillar-detail" x="422" y="738">Social</text>
    <text class="pillar-detail" x="512" y="738">Future</text>
    <text class="pillar-detail" x="602" y="738">Ready</text>
  </g>

  <text class="pillar" x="721" y="627">And</text>

  <g class="pillar-collaborating">
    <text class="pillar" x="940" y="627">Collaborating</text>
    <line class="branch" x1="940" y1="634" x2="893" y2="683"/>
    <line class="branch" x1="940" y1="634" x2="988" y2="683"/>
    <text class="pillar-detail" x="882" y="707">Staff</text>
    <text class="pillar-detail" x="990" y="707">Parent</text>
    <text class="pillar-detail" x="1025" y="733">Partnerships</text>
    <text class="pillar-detail" x="928" y="769">Team</text>
    <text class="pillar-detail" x="928" y="793">Players</text>
  </g>

  <g class="school-signature">
    <circle class="school-mark" cx="438" cy="1338" r="22"/>
    <text class="school-name" x="478" y="1356">Brindlewood Elementary School</text>
  </g>
</svg>
</body>
</html>
```